New Business Card Design Project

We require a business card design for Vexalund, a newly established Indian company.
Our focus is on the development, manufacturing, and export of a diverse array of pharmaceutical products on a global scale. The card should convey a professional appearance, as our primary markets are in Africa, China, and Southeast Asian nations.
We envision a two-sided business card, with the reverse side dedicated to a logo set against a solid color or an elegantly designed pattern. The corners should be rounded. We would appreciate seeing both horizontal and vertical design options. We trust the designer to utilize their expertise in creating this design.

The content for the business card is included in the attached Word file.

Target Market(s)

Our primary markets are in Africa, China, and Southeast Asian, Latin America, Maldives, Sri Lanka

Industry/Entity Type

Pharmaceutical Manufacturing and Export

Contact Information for Business Card

Colors

Designer to choose colors to be used in the design.

Requirements
Must have
• The reverse side of the business card features solely the logo along with the tagline, "Remedies of Life."
Should not have
• The logo should not exceed two instances, encompassing both the front and back sides of the card.

```html
<!DOCTYPE html>
<html lang="en">
<head>
<meta charset="utf-8">
<title>Vexalund Business Card</title>
<link href="https://fonts.googleapis.com/css2?family=Poppins:wght@300;400;600;700&family=Open+Sans:wght@400;600&display=swap" rel="stylesheet">
<style>
  :root {
    --bg: #222222;
    --brand-blue: #27a4e0;
    --brand-blue-deep: #1a8cc8;
    --brand-coral: #ef604a;
    --tab-red: #e41e26;
    --ink: #1b1b1b;
    --paper: #ffffff;
    --tint-blue: #e4f0fa;
    --tint-coral: #fde6e0;
  }
  * { margin: 0; padding: 0; box-sizing: border-box; }
  html, body { width: 1200px; height: 711px; overflow: hidden; background: var(--bg); }
  .stage {
    position: relative; width: 1200px; height: 711px;
    display: flex; align-items: center; justify-content: center; gap: 48px;
  }
  .card {
    position: relative; width: 520px; height: 297px;
    border-radius: 22px; overflow: hidden;
    border: 3px solid var(--brand-coral);
    box-shadow: 0 18px 36px rgba(0,0,0,.55);
  }

  /* Back side */
  .card-back { background: var(--brand-blue); }
  .back-pattern {
    position: absolute; inset: 0;
    background: linear-gradient(160deg, #3cb2e8 0%, var(--brand-blue) 45%, var(--brand-blue-deep) 100%);
  }
  .back-brand {
    position: absolute; left: 40px; top: 118px;
    display: flex; align-items: center; gap: 8px;
    font-family: 'Poppins', sans-serif; font-weight: 600; font-size: 17px;
    color: var(--paper);
  }
  .brand-dot { width: 12px; height: 12px; border-radius: 50%; background: var(--paper); }
  .tagline {
    position: absolute; right: 34px; bottom: 30px;
    font-family: 'Poppins', sans-serif; font-weight: 400; font-size: 16px;
    letter-spacing: .5px; color: var(--paper);
  }

  /* Front side */
  .card-front { background: var(--paper); }
  .front-decoration {
    position: absolute; left: 0; top: 40px; width: 300px; height: 257px;
    background: radial-gradient(ellipse at 30% 70%, var(--tint-blue) 0%, rgba(228,240,250,0) 55%),
                radial-gradient(ellipse at 70% 40%, var(--tint-coral) 0%, rgba(253,230,224,0) 60%);
  }
  .front-content {
    position: absolute; right: 34px; top: 24px;
    display: flex; flex-direction: column; align-items: flex-end; text-align: right;
  }
  .front-brand {
    display: flex; align-items: center; gap: 8px;
    font-family: 'Poppins', sans-serif; font-weight: 700; font-size: 32px;
    color: var(--brand-blue); line-height: 1;
  }
  .front-brand .brand-dot { width: 16px; height: 16px; background: var(--brand-coral); }
  .person {
    margin-top: 16px; font-family: 'Poppins', sans-serif; font-size: 21px; line-height: 1.1;
  }
  .person-first { font-weight: 700; color: var(--brand-blue); }
  .person-last { font-weight: 300; color: var(--brand-coral); }
  .role {
    font-family: 'Open Sans', sans-serif; font-size: 12px; color: var(--ink); letter-spacing: .5px;
  }
  .address {
    margin-top: 14px; font-family: 'Open Sans', sans-serif; font-size: 11px;
    color: var(--brand-blue); line-height: 1.4;
  }
  .contacts { margin-top: 10px; list-style: none; }
  .contacts li {
    display: flex; align-items: center; justify-content: flex-end; gap: 7px;
    font-family: 'Open Sans', sans-serif; font-size: 11.5px; color: var(--ink); line-height: 1.55;
  }
  .contacts svg { width: 11px; height: 11px; flex: none; }
  .role-tab {
    position: absolute; right: 0; top: 86px; width: 14px; height: 34px; background: var(--tab-red);
  }
</style>
</head>
<body>
<main class="stage">
  <section class="card card-back" aria-label="Card back">
    <div class="back-pattern" role="img" aria-label="Repeating blue capsule pattern"></div>
    <div class="back-brand"><span class="brand-dot"></span>Vexalund</div>
    <p class="tagline">Remedies of Life.</p>
  </section>

  <section class="card card-front" aria-label="Card front">
    <div class="front-decoration" role="img" aria-label="Large faint blue and coral capsule decoration"></div>
    <div class="role-tab"></div>
    <div class="front-content">
      <div class="front-brand"><span class="brand-dot"></span>Vexalund</div>
      <p class="person"><span class="person-first">Arjun</span> <span class="person-last">K. Malvade</span></p>
      <p class="role">CEO</p>
      <p class="address">12, Nilgiri Nagar,<br>Pune, 411038, India</p>
      <ul class="contacts">
        <li>+91 98765 43210
          <svg viewBox="0 0 12 12"><rect x="3" y="1" width="6" height="10" rx="1" fill="none" stroke="#ef604a" stroke-width="1.2"/></svg>
        </li>
        <li>www.vexalund.com
          <svg viewBox="0 0 12 12"><circle cx="6" cy="6" r="5" fill="none" stroke="#27a4e0" stroke-width="1.2"/><path d="M1 6h10M6 1c-2.5 3-2.5 7 0 10M6 1c2.5 3 2.5 7 0 10" fill="none" stroke="#27a4e0" stroke-width="1"/></svg>
        </li>
        <li>amalvade@vexalund.com
          <svg viewBox="0 0 12 12"><rect x="1" y="2.5" width="10" height="7" fill="none" stroke="#ef604a" stroke-width="1.2"/><path d="M1 2.5l5 4 5-4" fill="none" stroke="#ef604a" stroke-width="1.1"/></svg>
        </li>
      </ul>
    </div>
  </section>
</main>
</body>
</html>
```